Website for a company offering full serivce charging solutions for electric cars

The company "tanu-werk" (english: "tanu-works") offering all-in-one-solutions for charging infrastructure for electric mobility.

There are four products:
1- Wallboxes for single-family homes
2- Solutions for property devloper/-management for property parking space
3- All-in-one-charging solution for municipalities/communities
4- Solutions for tourism/hotels/holiday appartments

The Website structure:
1. Main Page
2.1. Product Page Single Homes
2.2. Product Page Property Management / Parking
2.3. Product Page Municipality
2.4. Product Page Tourism
3. Contact Form / Request for information
4. Imprint / Legal

The Website should be built on Wordpress with a powerful possibility to simply add/modify specific landing pages.

We would like you to implement the website later and also maintain it if possible, but we would be able to do minor modifications by ourselfs (for A/B-Testing)

The website should be clear and simple, easy to understand.
Target group is mainly B2C without deeper knowledge of that topic.

It should suggest, that we will provide a very simple way to get the charging infrastructure done.

We need a contact form, maybe we will use Hubspot later.

Attached you will find a draft of the main page and a landing page (for 2.2) - it is just the content, please ignore the design. We would love to let you create a suitable design.
Also you will find some drafts a bit different for the same story.

I added also a few stock photos, but they don't need to be used! If you have better ideas, you are welcome!

Industry/Entity Type

Charging/Electric mobility

Number of Pages Required

2 page

Font styles to use
Sans Serif

Requirements
Must have
• Based on Wordpress, and the designer should be able to implement it on Wordpress on a later step

```html
<!DOCTYPE html>
<html lang="de">
<head>
<meta charset="utf-8">
<title>tanu-werk – Ladelösungen aus einer Hand</title>
<link href="https://fonts.googleapis.com/css2?family=Playfair+Display:wght@500;600;700&family=Poppins:wght@400;500&display=swap" rel="stylesheet">
<style>
  :root{
    --purple:#5b45b5;
    --pink:#e6008a;
    --ink:#1d1d24;
    --text:#2c2c34;
    --gray:#ecedf0;
    --white:#ffffff;
  }
  *{box-sizing:border-box;margin:0;padding:0}
  html,body{width:1200px;height:2878px;overflow:hidden}
  body{position:relative;background:var(--white);font-family:"Poppins",sans-serif;color:var(--text)}
  .abs{position:absolute}

  /* header */
  .site-header{left:0;top:0;width:1200px;height:98px;background:var(--white)}
  .brand{left:37px;top:28px;display:flex;align-items:center;gap:10px;font-size:24px;font-weight:500;color:var(--ink)}
  .brand-dot{width:26px;height:26px;border-radius:50%;background:var(--pink)}
  .main-nav{right:45px;top:28px;display:flex;align-items:center;gap:33px;font-size:16px;color:var(--ink)}
  .btn-login{border:2.5px solid var(--purple);border-radius:5px;padding:9px 26px;font-weight:500;font-size:15px;margin-left:3px}

  /* hero */
  .hero-photo{left:0;top:98px;width:1200px;height:672px;
    background:linear-gradient(100deg,#dfe7f2 0%,#c8d6ea 35%,#8fb0e6 58%,#2f68e0 80%,#0f3fcf 100%);
    clip-path:polygon(0 0,100% 0,100% 615px,96% 625px,92% 612px,86% 630px,80% 618px,74% 640px,68% 626px,62% 660px,57% 672px,52% 650px,46% 640px,40% 632px,33% 644px,26% 628px,20% 638px,13% 626px,7% 640px,3% 628px,0 635px)}
  .hero-ring{left:143px;top:176px;width:432px;height:432px;border-radius:50%;border:13px solid var(--pink);background:var(--white);text-align:center;padding-top:88px}
  .hero-title{font-family:"Playfair Display",serif;font-weight:600;font-size:42px;line-height:46px}
  .hero-title .pink{color:var(--pink)}
  .hero-title .purple{color:var(--purple)}
  .hero-lead{font-size:19px;line-height:31px;color:var(--ink);margin:14px auto 0;width:340px}
  .btn{display:inline-block;background:var(--purple);color:var(--white);font-weight:500;font-size:15px;border-radius:3px;text-align:center}
  .hero-ring .btn{width:188px;height:50px;line-height:50px;margin-top:24px}

  /* company */
  .company{left:112px;top:896px;width:440px}
  .section-title{font-family:"Playfair Display",serif;font-weight:700;font-size:38px;color:var(--ink);letter-spacing:.5px}
  .company p{font-size:16px;line-height:26px;margin-top:14px}
  .company .section-title{margin-bottom:18px}
  .company .btn{width:188px;height:50px;line-height:50px;margin-top:24px}
  .company-accent{left:610px;top:837px;width:458px;height:456px;border-radius:50%;background:var(--purple)}
  .company-photo{left:634px;top:837px;width:456px;height:456px;border-radius:50%;
    background:radial-gradient(circle at 40% 50%,#f2a08e 0%,#b9c6dc 18%,#dce4ef 45%,#9fb1cf 100%)}

  /* services */
  .services{left:0;top:1381px;width:1200px;height:1140px;background:var(--gray)}
  .services-title{left:0;top:1456px;width:1200px;text-align:center}
  .card{top:1526px;width:350px;height:874px;border-radius:28px;background:var(--white);padding:20px 22px 0 32px;box-shadow:0 6px 14px rgba(0,0,0,.08)}
  .card.private{left:37px}
  .card.business{left:424px;background:var(--purple);color:var(--white)}
  .card.municipal{left:810px}
  .card h3{font-family:"Playfair Display",serif;font-weight:600;font-size:22px;color:var(--purple);text-align:center;margin-bottom:14px;margin-left:-10px}
  .card.business h3{color:var(--white)}
  .card ul{list-style:none}
  .card li{position:relative;padding-left:24px;font-size:14.6px;line-height:23px;margin-bottom:9px}
  .card li::before{content:"";position:absolute;left:0;top:6px;width:9px;height:9px;border-radius:50%;border:2.5px solid var(--purple)}
  .card.business li::before{border-color:var(--white)}
  .card ul.sub{margin:6px 0 0 0}
  .card ul.sub li{margin-bottom:2px}
  .card ul.sub li::before{border:none;border-right:1.6px solid var(--white);border-bottom:1.6px solid var(--white);border-radius:0;width:7px;height:7px;transform:rotate(-45deg);left:-1px;top:8px}
  .card ul.sub{margin-left:-24px}

  /* footer */
  .site-footer{left:0;top:2470px;width:1200px;height:408px;background:var(--pink);
    clip-path:polygon(0 52px,6% 30px,12% 42px,18% 20px,24% 36px,30% 48px,36% 28px,42% 44px,47% 10px,51% 0,55% 22px,60% 34px,66% 18px,72% 30px,78% 12px,84% 28px,90% 16px,95% 34px,100% 24px,100% 100%,0 100%)}
  .footer-brand{left:0;top:2615px;width:1200px;display:flex;justify-content:center;align-items:center;gap:12px;color:var(--white);font-size:34px;font-weight:500}
  .footer-brand .brand-dot{width:36px;height:36px;background:var(--white)}
  .footer-nav{left:0;top:2698px;width:1200px;display:flex;justify-content:center;gap:30px;color:var(--white);font-size:16px}
  .footer-nav .sep{opacity:.9}
  .social{left:0;top:2757px;width:1200px;display:flex;justify-content:center;gap:10px}
  .social span{width:36px;height:36px;border-radius:50%;border:2px solid var(--white)}
  .footer-rule{left:112px;top:2814px;width:976px;height:1px;background:rgba(255,255,255,.7)}
  .copyright{left:0;top:2832px;width:1200px;text-align:center;color:var(--white);font-size:15px}
</style>
</head>
<body>

<header class="site-header abs">
  <div class="brand abs"><span class="brand-dot"></span>tanu-werk.de</div>
  <nav class="main-nav abs">
    <span>Lösungen</span><span>Unternehmen</span><span>Dienstleistungen</span><span>Karriere</span><span>Kontakt</span>
    <span class="btn-login">EINLOGGEN</span>
  </nav>
</header>

<div class="hero-photo abs" role="img" aria-label="Ladestecker steckt in der beleuchteten Ladebuchse eines Elektroautos"></div>
<div class="hero-ring abs">
  <h1 class="hero-title"><span class="pink">tanu-werk ist</span><br><span class="purple">Ihr Partner</span></h1>
  <p class="hero-lead">wenn das Laden nicht nur einfach, sondern die Umsetzung auch aus einer Hand kommen soll</p>
  <span class="btn">LOSLEGEN</span>
</div>

<section class="company abs">
  <h2 class="section-title">UNTERNEHMEN</h2>
  <p>Wir bieten Lösungen sowohl für Privatkunden, Geschäftskunden als auch Kommunen an, die schnell, fair und ohne Eigenleistung zu einer smarten Ladelösung für E-Fahrzeuge kommen möchten.</p>
  <p>Von der Beratung, über die Installation, Inbetriebnahme bis zur Abrechnung und Wartung bekommen Sie bei tanu-werk alles aus einer Hand. Auf Wunsch vermieten wir auch die Ladetechnik und</p>
  <span class="btn">ERFAHREN SIE MEHR</span>
</section>
<div class="company-accent abs"></div>
<div class="company-photo abs" role="img" aria-label="Ladekabel in der Ladebuchse eines weißen Elektroautos"></div>

<section class="services abs"></section>
<h2 class="section-title services-title abs">UNSERE DIENSTLEISTUNGEN</h2>

<article class="card private abs">
  <h3>Als Privatkunde</h3>
  <ul>
    <li>Bestandsanalyse mit umfangreicher Beratung über die Möglichkeiten der Umsetzung</li>
    <li>Prüfung und Übernahme der Anmeldung verfügbarer Fördermöglichkeiten</li>
    <li>Auswahl an smarten Wallbox Lösungen, passend für Ihr Fahrzeug und Ihre Bedürfnisse</li>
    <li>Installation inkl. aller notwendigen Materialien und Tätigkeiten (Durchbrüche, Erdarbeiten, etc.)</li>
    <li>Inbetriebnahme und Einweisung in die Ladetechnik</li>
    <li>Jährlich technische Wartung nach DGUV3</li>
    <li>Reparaturservice, unter Berücksichtigung der geltenden Garantie Ansprüche</li>
  </ul>
</article>

<article class="card business abs">
  <h3>Als Geschäftskunde</h3>
  <ul>
    <li>Durchführung einer individuellen Bedarfsanalyse inkl. Ermittlung der Anforderungen für:
      <ul class="sub">
        <li>Haus- und Immobilienverwaltungen</li>
        <li>Dienstleistungs- und Handelsunternehmen</li>
        <li>Hotel und Beherbergungsbetriebe</li>
        <li>Parkraum- und Parkhausbetreiber</li>
        <li>Tourismus, Sport- und Freizeiteinrichtungen</li>
      </ul>
    </li>
    <li>Planung und Projektierung des Installationsaufwands inkl. Materialverbrauch</li>
    <li>Leasing oder Kauf der Hardware</li>
    <li>Normgerechte Installation der Ladeinfrastruktur inkl. Durchbruch-, Brandschutz- und Erdarbeiten</li>
    <li>Bei Bestandsbauten Integration der Ladeinfrastruktur in die Gebäudesystemtechnik und ggf. Anpassung des Netzanschlusses</li>
    <li>Inbetriebnahme der Anlage inkl. Prüf- und Messprotokollen</li>
    <li>Wiederkehrende technische Prüfung der Anlage nach DGUV 3</li>
    <li>Austausch und Reparatur Service</li>
    <li>Unterstützung bei der mtl. Nutzungsabrechnung und Einbindung in Ihre vorhandene</li>
    <li>ODER direkte Abrechnung mit den Nutzern</li>
  </ul>
</article>

<article class="card municipal abs">
  <h3>Als Kommune</h3>
  <ul>
    <li>Konzeptionierung möglicher Ladeinfrastrukturen innerhalb Ihrer Gemeinde</li>
    <li>Planung und Projektsteuerung inkl. sämtlicher behördlicher Genehmigungsverfahren und Beantragung von Fördermitteln</li>
    <li>Fachgerechte Installation und Inbetriebnahme</li>
    <li>Regelmäßige Wartung gemäß Vorschrif</li>
    <li>Reparatur und Kundenservice</li>
    <li>Direkte Abrechnung mit dem Nutzer</li>
    <li>Beteiligung der Gemeinde am Umsatz</li>
    <li>Möglichkeit der Integration von Bonusprogrammen, mit denen der lokale Einzelhandel beworben wird</li>
  </ul>
</article>

<footer class="site-footer abs"></footer>
<div class="footer-brand abs"><span class="brand-dot"></span>tanu-werk.de</div>
<nav class="footer-nav abs">
  <span>AGB</span><span class="sep">|</span><span>Datenschutzerklärung</span><span class="sep">|</span><span>Impressum</span><span class="sep">|</span><span>Kontakt</span><span class="sep">|</span><span>Karriere</span><span class="sep">|</span><span>FAQs</span>
</nav>
<div class="social abs" aria-label="Soziale Netzwerke"><span></span><span></span><span></span></div>
<div class="footer-rule abs"></div>
<p class="copyright abs">2022 ©tanu-werk GmbH</p>

</body>
</html>
```